Every Shelf Set Neatly or ESN Organized needs a business card design. ESN Organized is a professi

We need a business card design that is clean, sharp and conveys a sense of organization. I already have a logo.

Target Market(s)

Families (specifically mothers), small business owners, parents, seniors

Industry/Entity Type

Business

Contact Information for Business Card

My website is www.esnorganized-example.com and my Facebook page is http://www.sociallink-example.com/everyshelfsetneatly. The phone number is 418-552-7094 and I want to be listed as Lorna M. Pelham, Owner

Requirements
Must have
• My logo.

```html
<!DOCTYPE html>
<html lang="en">
<head>
<meta charset="utf-8">
<title>ESN Organized – Business Card</title>
<link rel="stylesheet" href="https://fonts.googleapis.com/css2?family=Arimo:wght@400;700&display=swap">
<style>
  :root {
    --backdrop: #3a3b3e;
    --card: #ffffff;
    --brand-blue: #1c82dc;
    --brand-blue-deep: #0f6cc4;
    --brand-blue-wash: #d6e8f8;
    --ink: #2b2b2b;
    --ink-soft: #555a60;
  }
  * { box-sizing: border-box; margin: 0; padding: 0; }
  html, body {
    width: 1200px; height: 950px; overflow: hidden;
    background: var(--backdrop);
    font-family: "Arimo", Arial, sans-serif;
  }
  .canvas { position: relative; width: 1200px; height: 950px; }
  .card {
    position: absolute; left: 250px;
    width: 700px; height: 400px;
    background: var(--card);
    overflow: hidden;
  }
  .card--back { top: 50px; display: flex; align-items: center; justify-content: center; }
  .card--front { top: 500px; }

  .logo { display: flex; align-items: center; gap: 16px; }
  .logo__dot { width: 26px; height: 26px; border-radius: 50%; background: var(--brand-blue); }
  .logo__name {
    font-size: 44px; font-weight: 400; color: var(--ink);
    letter-spacing: 4px; white-space: nowrap;
  }

  .decor-area {
    position: absolute; left: 0; right: 0; height: 120px;
  }
  .decor-area--top {
    top: 0;
    background: linear-gradient(to bottom, var(--brand-blue-wash), var(--card));
  }
  .decor-area--bottom {
    bottom: 0;
    background: linear-gradient(to top, var(--brand-blue-wash), var(--card));
  }

  .details {
    position: absolute; left: 0; right: 0; top: 156px;
    text-align: center;
  }
  .details__heading { white-space: nowrap; }
  .details__name {
    font-size: 27px; font-weight: 700; color: var(--brand-blue);
  }
  .details__role { font-size: 17px; font-weight: 700; color: var(--ink); }
  .details__rule {
    margin: 12px auto; width: 640px; height: 1px;
    background: linear-gradient(to right, transparent, var(--brand-blue) 30%, var(--brand-blue) 70%, transparent);
  }
  .details__contacts {
    display: flex; justify-content: center; align-items: center; gap: 18px;
    font-size: 16px; color: var(--ink-soft); white-space: nowrap;
  }
  .details__label { color: var(--brand-blue); font-weight: 700; }
  .details__social { display: inline-flex; align-items: center; gap: 6px; }
  .details__social-mark { width: 15px; height: 15px; background: var(--brand-blue); }
</style>
</head>
<body>
<main class="canvas">
  <section class="card card--back" aria-label="Card back">
    <div class="logo">
      <span class="logo__dot"></span>
      <span class="logo__name">ESN Organized</span>
    </div>
  </section>

  <section class="card card--front" aria-label="Card front">
    <div class="decor-area decor-area--top" role="img" aria-label="Decorative blue rounded stripe motif"></div>
    <div class="decor-area decor-area--bottom" role="img" aria-label="Decorative blue rounded stripe motif"></div>
    <div class="details">
      <p class="details__heading"><span class="details__name">Lorna M. Pelham -</span> <span class="details__role">Owner</span></p>
      <div class="details__rule"></div>
      <p class="details__contacts">
        <span><span class="details__label">P:</span> 418-552-7094</span>
        <span><span class="details__label">W:</span> www.esnorganized-example.com</span>
        <span class="details__social"><span class="details__social-mark"></span>everyshelfsetneatly</span>
      </p>
    </div>
  </section>
</main>
</body>
</html>
```